Business Card Design

We need a business card designed for our new company. Prefer a black card with white logo & writing.

Contact Information for Business Card

Ted Galloway, address: 7-4812 Fernhollow Road, Abbotsford, BC, V3K 8R2, Office Phone: 604-712-3390, Cell: 604-947-2164, Email: ted@resinworkshub.ca

Colors

Designer to choose only greyscale colors for use in the design.

```html
<!DOCTYPE html>
<html lang="en">
<head>
<meta charset="utf-8">
<title>Resin Works Hub – Business Card</title>
<link href="https://fonts.googleapis.com/css2?family=Poppins:wght@300;400;700&display=swap" rel="stylesheet">
<style>
  :root {
    --backdrop: #232323;
    --card: #1e1e20;
    --ink: #ffffff;
    --ink-soft: #d9d9d9;
    --rule: #8a8a8a;
    --wordmark-back: #3a3a3c;
    --frame-back: #4a4a4c;
  }
  * { margin: 0; padding: 0; box-sizing: border-box; }
  html, body {
    width: 1200px; height: 780px; overflow: hidden;
    background: var(--backdrop);
    font-family: "Poppins", sans-serif;
    color: var(--ink);
  }
  .canvas {
    position: relative; width: 1200px; height: 780px;
    display: flex; align-items: center; justify-content: center; gap: 40px;
  }
  .card {
    position: relative; width: 540px; height: 310px;
    background: var(--card);
    box-shadow: 0 18px 40px rgba(0,0,0,.55);
    overflow: hidden;
  }
  /* front */
  .edge-bar {
    position: absolute; width: 9px; height: 140px; background: var(--ink);
  }
  .edge-bar--right { right: 22px; top: 0; }
  .edge-bar--left { left: 22px; bottom: 0; }
  .brand {
    position: absolute; left: 40px; top: 70px; width: 210px;
    text-align: center;
  }
  .brand__name {
    font-weight: 700; font-size: 30px; line-height: 1.05;
    letter-spacing: .5px; color: var(--ink); text-transform: uppercase;
  }
  .divider {
    position: absolute; left: 270px; top: 44px; width: 1px; height: 150px;
    background: linear-gradient(to bottom, transparent, var(--rule) 30%, var(--rule) 70%, transparent);
  }
  .contact {
    position: absolute; left: 300px; top: 44px;
  }
  .contact__name { font-size: 28px; line-height: 1; font-weight: 300; }
  .contact__name b { font-weight: 700; }
  .contact__role { font-size: 12px; font-weight: 300; color: var(--ink-soft); margin-top: 4px; }
  .contact__list { list-style: none; margin-top: 16px; }
  .contact__list li {
    display: flex; align-items: center; gap: 8px;
    font-size: 12.5px; font-weight: 300; line-height: 1.55;
  }
  .contact__list svg { width: 11px; height: 11px; flex: none; }
  .address {
    position: absolute; left: 40px; bottom: 34px;
    font-size: 14px; font-weight: 400; letter-spacing: .2px;
  }
  /* back */
  .card--back { display: flex; align-items: center; justify-content: center; }
  .back-frame {
    width: 300px; height: 190px;
    border: 2px solid var(--frame-back);
    display: flex; align-items: center; justify-content: center;
  }
  .back-wordmark {
    font-weight: 700; font-size: 34px; line-height: 1.1;
    text-align: center; text-transform: uppercase; color: var(--wordmark-back);
  }
</style>
</head>
<body>
<main class="canvas">
  <section class="card card--front" aria-label="Business card front">
    <span class="edge-bar edge-bar--right"></span>
    <span class="edge-bar edge-bar--left"></span>

    <div class="brand">
      <p class="brand__name">Resin<br>Works<br>Hub</p>
    </div>

    <span class="divider"></span>

    <div class="contact">
      <h1 class="contact__name"><b>Ted</b> Galloway</h1>
      <p class="contact__role">Founder &amp; CEO</p>
      <ul class="contact__list">
        <li>
          <svg viewBox="0 0 12 12" fill="none" stroke="#fff" stroke-width="1.3"><path d="M3 1.5 4.6 4 3.6 5.2a6 6 0 0 0 3.2 3.2L8 7.4l2.5 1.6-.8 1.7C5.5 10.8 1.2 6.5 1.3 2.3z"/></svg>
          604-712-3390
        </li>
        <li>
          <svg viewBox="0 0 12 12" fill="none" stroke="#fff" stroke-width="1.3"><rect x="3" y="1" width="6" height="10" rx="1"/><circle cx="6" cy="9" r=".5" fill="#fff"/></svg>
          604-947-2164
        </li>
        <li>
          <svg viewBox="0 0 12 12" fill="none" stroke="#fff" stroke-width="1.1"><circle cx="6" cy="6" r="5"/><ellipse cx="6" cy="6" rx="2.2" ry="5"/><path d="M1 6h10"/></svg>
          www.resinworkshub.ca
        </li>
        <li>
          <svg viewBox="0 0 12 12" fill="none" stroke="#fff" stroke-width="1.2"><rect x="1" y="2.5" width="10" height="7"/><path d="M1 2.5 6 6.5l5-4"/></svg>
          ted@resinworkshub.ca
        </li>
      </ul>
    </div>

    <p class="address">7-4812 Fernhollow Road, Abbotsford, BC, V3K 8R2.</p>
  </section>

  <section class="card card--back" aria-label="Business card back">
    <div class="back-frame">
      <p class="back-wordmark">Resin<br>Works Hub</p>
    </div>
  </section>
</main>
</body>
</html>
```